Road Construction Company needs business cards

We would like a new business card designed for our business.

We're a road construction company based in Qld, Australia.

Can the business card please have the following information on it.

Name: Warren Halbeck
Position: General Manager
Phone: 0472 915 348
Email: Warren.halbeck@tovrin.com.au
Address: 87 Marrow Ave, Pendlebay, QLD, 4023
Website: www.tovrin.com.au

Visually we'd like the card to be professional and simple.

Attached is our logo.

Our website is www.tovrin.com.au

Target Market(s)

Men aged 25-60

Contact Information for Business Card

As listed in project description

Font styles to use
Serif

Requirements
Must have
• Large logo on back of card

```html
<!DOCTYPE html>
<html lang="en">
<head>
<meta charset="UTF-8">
<title>Tovrin Business Card</title>
<link rel="stylesheet" href="https://fonts.googleapis.com/css2?family=Montserrat:wght@400;500;700&display=swap">
<style>
  :root {
    --backdrop: #2f3033;
    --brand-dark: #0c55a6;
    --brand-light: #2a9fd8;
    --ink: #1e1e1e;
    --paper: #ffffff;
  }
  * { margin: 0; padding: 0; box-sizing: border-box; }
  html, body {
    width: 1200px; height: 1059px; overflow: hidden;
    background: var(--backdrop);
    font-family: "Montserrat", sans-serif;
  }
  .card {
    position: absolute;
    border-radius: 18px;
    overflow: hidden;
  }
  .card--front {
    left: 256px; top: 100px; width: 688px; height: 391px;
    background: var(--paper);
  }
  .card--back {
    left: 253px; top: 537px; width: 694px; height: 394px;
    background: var(--brand-dark);
    display: flex; align-items: center; justify-content: center;
  }
  .brand-name {
    font-weight: 700;
    text-transform: uppercase;
    letter-spacing: 4px;
    line-height: 1;
  }
  .card--front .brand-name {
    position: absolute; left: 28px; top: 68px;
    font-size: 60px; color: var(--brand-dark);
  }
  .card--back .brand-name {
    font-size: 78px; color: var(--paper);
  }
  .accent-bar {
    position: absolute; left: 0; top: 214px;
    width: 13px; height: 43px;
    background: var(--brand-dark);
  }
  .person-name {
    position: absolute; left: 30px; top: 212px;
    font-size: 29px; font-weight: 700; line-height: 34px;
    color: var(--brand-dark);
  }
  .person-name .surname { color: var(--brand-light); }
  .person-role {
    position: absolute; left: 30px; top: 244px;
    font-size: 17px; line-height: 20px; color: var(--ink);
  }
  .contact-list { list-style: none; }
  .contact-item {
    position: absolute; left: 29px;
    display: flex; align-items: center; gap: 8px;
    font-size: 16px; line-height: 20px; color: var(--ink);
    letter-spacing: 0.3px;
  }
  .contact-item svg { width: 13px; height: 13px; fill: var(--brand-dark); flex: none; }
  .contact-item--phone { top: 292px; }
  .contact-item--email { top: 318px; }
  .contact-item--web { top: 344px; }
  .address-divider {
    position: absolute; left: 396px; top: 328px;
    width: 1.5px; height: 31px; background: var(--brand-dark);
  }
  .address {
    position: absolute; left: 414px; top: 323px;
    font-style: normal; font-size: 16px; line-height: 20px;
    color: var(--ink); letter-spacing: 0.3px;
  }
</style>
</head>
<body>
  <section class="card card--front">
    <div class="brand-name">Tovrin</div>
    <div class="accent-bar"></div>
    <h1 class="person-name">Warren <span class="surname">Halbeck</span></h1>
    <p class="person-role">General Manager</p>
    <ul class="contact-list">
      <li class="contact-item contact-item--phone">
        <svg viewBox="0 0 24 24" aria-hidden="true"><path d="M6.6 10.8a15.1 15.1 0 0 0 6.6 6.6l2.2-2.2a1 1 0 0 1 1-.25 11.4 11.4 0 0 0 3.6.6 1 1 0 0 1 1 1V20a1 1 0 0 1-1 1A17 17 0 0 1 3 4a1 1 0 0 1 1-1h3.5a1 1 0 0 1 1 1c0 1.25.2 2.45.6 3.6a1 1 0 0 1-.25 1z"/></svg>
        0472 915 348
      </li>
      <li class="contact-item contact-item--email">
        <svg viewBox="0 0 24 24" aria-hidden="true"><path d="M2 5h20v14H2z" opacity="0"/><path d="M2 5h20v2l-10 6L2 7z"/><path d="M2 9l10 6 10-6v10H2z"/></svg>
        Warren.halbeck@tovrin.com.au
      </li>
      <li class="contact-item contact-item--web">
        <svg viewBox="0 0 24 24" aria-hidden="true"><path d="M12 2a10 10 0 1 0 0 20 10 10 0 0 0 0-20zm0 2c.9 1.2 1.6 2.6 2 4h-4c.4-1.4 1.1-2.8 2-4zM4.3 14a8 8 0 0 1 0-4h3.4a16 16 0 0 0 0 4zm.8 2h3c.3 1.3.8 2.5 1.4 3.6A8 8 0 0 1 5.1 16zm3-8h-3a8 8 0 0 1 4.4-3.6C8.9 5.5 8.4 6.7 8.1 8zM12 20c-.9-1.2-1.6-2.6-2-4h4c-.4 1.4-1.1 2.8-2 4zm2.3-6H9.7a14 14 0 0 1 0-4h4.6a14 14 0 0 1 0 4zm.2 5.6c.6-1.1 1.1-2.3 1.4-3.6h3a8 8 0 0 1-4.4 3.6zm1.8-5.6a16 16 0 0 0 0-4h3.4a8 8 0 0 1 0 4z"/></svg>
        www.tovrin.com.au
      </li>
    </ul>
    <div class="address-divider"></div>
    <address class="address">87 Marrow Ave,<br>Pendlebay, QLD, 4023</address>
  </section>

  <section class="card card--back">
    <div class="brand-name">Tovrin</div>
  </section>
</body>
</html>
```